Creative Alcoholic Beverage Package Design Needed!

We need a packaging design for a new alcoholic beverage, including the brand name. Flavours will include Sangria and Margarita, and future line extensions as well. Package will be a box (see attached dieline and example of a competitive product) in a 3 liter format. The dimensions of the box need to match the dieline, but we can be creative on the printing of the box. The product inside will be of high-quality, so the design needs to match this
Updates

Need extra days to review

Target Market(s)

25 to 40 year old, 70% female, 30% male

Colors

Designer to choose colors to be used in the design.

Requirements
Must have
• Be attractive, colourful, modern
• clearly mention the flavour, and show the components of the flavour (Sangria : red wine and citrus) - Margarita (mexican inspiration, lime, etc.)
• Have a clear "brand name" along with the flavours
• Mention the quantity (3 liters), alcohol level : 10% alc./vol.

```html
<!DOCTYPE html>
<html lang="en">
<head>
<meta charset="utf-8">
<title>Château Solenne – Sangria 3 L box dieline</title>
<link rel="stylesheet" href="https://fonts.googleapis.com/css2?family=Marcellus&display=swap">
<style>
  :root{
    --page:#ffffff;
    --backdrop:#d6d6d6;
    --gold:#c9a66b;
    --pink:#f06fa6;
    --ink:#111111;
    --label-dark:#1e1e1e;
    --dieline:#2b2f8f;
    --cut:#e0262d;
    --wine-deep:#7a0d14;
    --wine-light:#f3b3c0;
  }
  html,body{margin:0;padding:0;overflow:hidden;width:1200px;height:1200px;background:var(--backdrop);}
  .canvas{display:block;width:1200px;height:1200px;}
  .serif{font-family:"Marcellus",Georgia,serif;}
  .brand-line{fill:var(--ink);}
  .gold-text{fill:var(--gold);}
  .white-text{fill:#fff;}
  .ink-text{fill:var(--ink);}
  .dieline{fill:none;stroke:var(--dieline);stroke-width:1.5;}
  .cutline{fill:none;stroke:var(--cut);stroke-width:1.2;}
  .fold-dash{fill:none;stroke:var(--dieline);stroke-width:1.3;stroke-dasharray:6 8;}
  .print-band{fill:var(--pink);}
  .gold-bar{fill:var(--gold);}
  .scale-bar{fill:var(--ink);}
</style>
</head>
<body>
<svg class="canvas serif" viewBox="0 0 1280 1280" width="1200" height="1200" xmlns="http://www.w3.org/2000/svg">
  <defs>
    <linearGradient id="wine-pour" x1="1" y1="0" x2="0" y2="1">
      <stop offset="0" stop-color="var(--wine-light)"/>
      <stop offset="0.45" stop-color="#c0404f"/>
      <stop offset="1" stop-color="var(--wine-deep)"/>
    </linearGradient>

    <!-- Front / back main panel artwork, 367 x 524 -->
    <g id="main-panel">
      <rect class="wine-photo" x="105" y="185" width="255" height="262" rx="28" fill="url(#wine-pour)" opacity="0.85"
            role="img" aria-label="Glass of red sangria with a pink splash pouring in"/>
      <text class="gold-text" x="185" y="70" font-size="26" text-anchor="middle">CHÂTEAU</text>
      <text class="brand-line" x="185" y="124" font-size="54" text-anchor="middle">SOLENNE</text>
      <rect class="gold-bar" x="32" y="133" width="306" height="2"/>
      <g class="flavour-label">
        <rect x="0" y="294" width="183" height="62" fill="var(--label-dark)"/>
        <rect x="2" y="296" width="179" height="40" class="gold-bar"/>
        <text class="ink-text" x="91" y="328" font-size="32" text-anchor="middle">SANGRIA</text>
        <text class="white-text" x="91" y="351" font-size="14" text-anchor="middle">RED WINE AND CITRUS</text>
      </g>
      <g class="volume">
        <text class="gold-text" x="48" y="492" font-size="40" text-anchor="middle">3</text>
        <text class="ink-text" x="48" y="512" font-size="15" text-anchor="middle">LITRES</text>
      </g>
      <g class="abv">
        <text class="gold-text" x="308" y="492" font-size="40" text-anchor="middle">10%</text>
        <text class="ink-text" x="310" y="512" font-size="15" text-anchor="middle">ALC./VOL</text>
      </g>
    </g>

    <!-- Side panel artwork, 180 x 524 -->
    <g id="side-panel">
      <rect class="wine-photo" x="12" y="318" width="158" height="196" rx="22" fill="url(#wine-pour)" opacity="0.85"
            role="img" aria-label="Small glass of red sangria with a pink splash"/>
      <text class="gold-text" x="90" y="58" font-size="12" text-anchor="middle">CHÂTEAU</text>
      <text class="brand-line" x="90" y="84" font-size="26" text-anchor="middle">SOLENNE</text>
      <rect class="gold-bar" x="17" y="89" width="144" height="1.5"/>
      <g class="tasting-notes">
        <rect class="gold-bar" x="17" y="135" width="144" height="11"/>
        <text class="ink-text" x="90" y="144" font-size="9" text-anchor="middle">TASTING NOTES</text>
        <text class="ink-text" x="90" y="155" font-size="9" text-anchor="middle">A PLEASING RED WINE AND</text>
        <text class="ink-text" x="90" y="165" font-size="9" text-anchor="middle">CITRUS .</text>
      </g>
      <g class="body-scale">
        <rect class="gold-bar" x="17" y="176" width="144" height="11"/>
        <text class="ink-text" x="90" y="185" font-size="9" text-anchor="middle">BODY</text>
        <rect class="scale-bar" x="17" y="197" width="144" height="5"/>
        <path class="scale-bar" d="M20 192h8l-4 5z M86 192h8l-4 5z M153 192h8l-4 5z"/>
        <text class="ink-text" x="17" y="217" font-size="8">LIGHT</text>
        <text class="ink-text" x="90" y="217" font-size="8" text-anchor="middle">MEDIUM</text>
        <text class="ink-text" x="167" y="217" font-size="8" text-anchor="end">FULL</text>
      </g>
      <g class="sweetness-scale">
        <rect class="gold-bar" x="17" y="235" width="144" height="11"/>
        <text class="ink-text" x="90" y="244" font-size="9" text-anchor="middle">SWEETNESS</text>
        <rect class="scale-bar" x="17" y="256" width="144" height="5"/>
        <path class="scale-bar" d="M27 251h8l-4 5z M66 251h8l-4 5z M108 251h8l-4 5z M146 251h8l-4 5z"/>
        <text class="ink-text" x="33" y="272" font-size="7" text-anchor="middle">DRY</text>
        <text class="ink-text" x="70" y="272" font-size="7" text-anchor="middle">MEDIUM</text>
        <text class="ink-text" x="70" y="280" font-size="7" text-anchor="middle">DRY</text>
        <text class="ink-text" x="113" y="272" font-size="7" text-anchor="middle">MEDIUM</text>
        <text class="ink-text" x="113" y="280" font-size="7" text-anchor="middle">SWEET</text>
        <text class="ink-text" x="150" y="272" font-size="7" text-anchor="middle">SWEET</text>
      </g>
      <text class="ink-text" x="91" y="300" font-size="9.5" text-anchor="middle">SERVE AT ROOM TEMPERATURE</text>
    </g>

    <!-- Side top flap with thumb notch -->
    <path id="side-top-flap" d="M0 118 V22 Q0 2 20 2 H48 Q58 2 58 14 Q58 48 90 48 Q122 48 122 14 Q122 2 132 2 H160 Q172 2 172 22 V118"/>
  </defs>

  <!-- sheet -->
  <rect x="46" y="183" width="1189" height="897" fill="var(--page)"/>
  <rect class="print-band" x="110" y="900" width="1112" height="195"/>

  <!-- glue flap -->
  <path class="dieline" d="M112 383 L62 395 V1040 Q62 1052 74 1052 H112"/>
  <line class="cutline" x1="62" y1="888" x2="118" y2="888"/>
  <line class="cutline" x1="62" y1="910" x2="118" y2="910"/>
  <line class="fold-dash" x1="80" y1="410" x2="80" y2="1030"/>
  <line class="fold-dash" x1="94" y1="410" x2="94" y2="1030"/>

  <!-- panel artwork -->
  <g transform="translate(118 376)"><use href="#side-panel"/></g>
  <g transform="translate(298 376)"><use href="#main-panel"/></g>
  <g transform="translate(673 376)"><use href="#side-panel"/></g>
  <g transform="translate(855 376)"><use href="#main-panel"/></g>

  <!-- body creases -->
  <rect class="cutline" x="118" y="376" width="1104" height="524"/>
  <line class="cutline" x1="298" y1="376" x2="298" y2="900"/>
  <line class="cutline" x1="670" y1="376" x2="670" y2="900"/>
  <line class="cutline" x1="855" y1="376" x2="855" y2="900"/>
  <line x1="118" y1="903" x2="1222" y2="903" stroke="var(--gold)" stroke-width="3"/>

  <!-- top flaps -->
  <g transform="translate(120 258)"><use class="dieline" href="#side-top-flap"/></g>
  <g transform="translate(676 258)"><use class="dieline" href="#side-top-flap"/></g>
  <path class="dieline" d="M305 376 V220 Q305 198 327 198 H642 Q664 198 664 220 V376"/>
  <rect class="dieline" x="406" y="258" width="156" height="52" rx="26"/>
  <path class="dieline" d="M861 376 V220 Q861 198 883 198 H1197 Q1219 198 1219 220 V376"/>
  <rect class="dieline" x="954" y="252" width="172" height="60" rx="26"/>
  <line class="cutline" x1="970" y1="252" x2="1110" y2="252"/>
  <line class="cutline" x1="430" y1="310" x2="540" y2="310"/>
  <g class="fold-dash">
    <line x1="135" y1="280" x2="145" y2="355"/><line x1="275" y1="280" x2="265" y2="355"/>
    <line x1="690" y1="280" x2="700" y2="355"/><line x1="830" y1="280" x2="820" y2="355"/>
  </g>

  <!-- bottom flaps -->
  <path class="dieline" d="M120 900 V1040 Q120 1052 132 1052 H280 Q292 1052 292 1040 V900"/>
  <path class="dieline" d="M305 900 V1060 Q305 1080 325 1080 H644 Q664 1080 664 1060 V900"/>
  <path class="dieline" d="M678 900 V1040 Q678 1052 690 1052 H838 Q850 1052 850 1040 V900"/>
  <path class="dieline" d="M861 900 V1060 Q861 1080 881 1080 H1200 Q1220 1080 1220 1060 V900"/>
  <g class="fold-dash">
    <line x1="135" y1="1035" x2="145" y2="920"/><line x1="275" y1="1035" x2="265" y2="920"/>
    <line x1="690" y1="1035" x2="700" y2="920"/><line x1="830" y1="1035" x2="820" y2="920"/>
  </g>

  <!-- tear-out window on second side -->
  <path class="cutline" d="M711 706 H812"/>
  <path d="M711 706 V840 H812 V706 M732 792 H795 V840 H732 Z" fill="none" stroke="var(--dieline)" stroke-width="1.2" stroke-dasharray="3 3"/>
</svg>
</body>
</html>
```